Ledgerwise Forge - WordPress Theme & Logo

Design a logo and Wordpress website design for Ledgerwise Forge. Ledgerwise Forge provides cryptocurrency development services to clients who need a team to create & continue developing a new cryptocurrency or who want to replace their current cryptocurrency development team. more details in the attached document.
Updates

Target Market(s)

Entrepreneurs who are building a business / platform that makes use of an underlying cryptocurrency.

Logo Text

LF or Ledgerwise Forge

Coding

Coded - Design and coding required

Font styles to use
Sans Serif

Requirements
Must have
• Professional logo, complete coded Wordpress theme for all pages, containing all specified links and buttons
Nice to have
• It would be nice if the buttons that are meant to integrate with Dealtrail contain the necessary code for that. I can provide any necessary Dealtrail details from my account.
Should not have
• Slow loading time

```html
<!DOCTYPE html>
<html lang="en">
<head>
<meta charset="utf-8">
<title>Ledgerwise Forge</title>
<link href="https://fonts.googleapis.com/css2?family=Exo+2:wght@500;600;700&family=Lato:wght@400;700&display=swap" rel="stylesheet">
<style>
:root{
  --teal:#14988a;
  --green:#178a3a;
  --ink:#1b1b1b;
  --text:#333;
  --pale:#d6f0e4;
  --cyan:#d9f4f4;
  --black:#000;
}
*{box-sizing:border-box;margin:0;padding:0}
html,body{width:1200px;height:3499px;overflow:hidden;background:#fff}
body{font-family:'Lato',sans-serif;color:var(--text);position:relative}
.page{position:relative;width:1200px;height:3499px;overflow:hidden}
.abs{position:absolute}
h1,h2,h3,h4,.brand,.nav a{font-family:'Exo 2',sans-serif}
a{text-decoration:none;color:inherit}

/* header */
.header{top:0;left:0;width:1200px;height:86px;background:#fff;z-index:5}
.brand{position:absolute;left:111px;top:8px;display:flex;align-items:center;gap:16px;font-size:23px;font-weight:500;color:var(--ink)}
.brand-mark{width:38px;height:38px;background:var(--teal)}
.contact{position:absolute;top:10px;left:580px;display:flex;align-items:center;gap:14px;font-size:15px;color:#333}
.contact .ico{width:32px;height:32px;border-radius:50%;background:#dff3ec;display:flex;align-items:center;justify-content:center}
.contact span+span.ico{margin-left:14px}
.social{display:flex;gap:10px;margin-left:26px}
.social i{width:12px;height:12px;border-radius:50%;background:var(--teal);display:block}
.nav{position:absolute;top:56px;left:183px;display:flex;gap:0;font-size:15.5px;font-weight:500;color:#222}
.nav a{padding:2px 12px}
.nav a.active{background:#dff3ec;color:var(--teal)}

/* hero */
.hero-bg{top:86px;left:0;width:1200px;height:690px;background:radial-gradient(circle at 840px 300px,#0d4b5a 0,#06222c 30%,#020a10 60%),linear-gradient(90deg,#0d5a66,#020b10)}
.hero-globe{top:160px;left:650px;width:430px;height:430px;border-radius:50%;background:radial-gradient(circle at 45% 40%,#1f7c8c,#0a3440 60%,#031014 100%);opacity:.85}
.hero-text{top:200px;left:111px;color:#fff}
.hero-text h1{font-size:43px;font-weight:600;line-height:51px;width:560px}
.hero-text p{margin-top:24px;font-size:15.5px}
.hero-text .btn{margin-top:28px}

/* buttons */
.btn{display:inline-flex;align-items:center;gap:8px;height:34px;padding:0 14px 0 4px;border-radius:17px;background:linear-gradient(90deg,var(--teal),var(--green));color:#fff;font-family:'Exo 2',sans-serif;font-size:14.5px;font-weight:600;text-transform:uppercase;white-space:nowrap}
.btn .dot{width:27px;height:27px;border-radius:50%;background:#fff;display:flex;align-items:center;justify-content:center}
.btn.outline{border:2px solid var(--teal)}

/* sections */
.title{left:0;width:1200px;text-align:center;font-size:34px;font-weight:500;color:var(--ink)}
.lead{text-align:center;font-size:15px;line-height:30px;color:#333}

.feature{width:280px;text-align:center}
.ring{width:158px;height:158px;margin:0 auto;border-radius:50%;border:4px solid var(--teal);border-right-color:#bfe6e0;display:flex;align-items:center;justify-content:center}
.ring.green{border-color:var(--green);border-right-color:#bfe6cc}
.ring .icon{width:70px;height:70px;border-radius:12px;background:#e9f3f2}
.feature h3{margin-top:22px;font-size:22px;font-weight:600;color:var(--ink)}
.feature p{margin-top:10px;font-size:15px;line-height:29px;color:#333}

.svc-title{left:0;width:1160px;text-align:center;top:1645px;color:#fff;font-size:35px;font-weight:600}
.card{top:1748px;width:236px;height:310px;display:flex;flex-direction:column;align-items:center;justify-content:center;text-align:center;color:#fff}
.card h4{font-size:21px;font-weight:600;line-height:27px;margin-bottom:12px;text-shadow:0 1px 3px rgba(0,0,0,.5)}
.card .btn{font-size:14px}

.tcard{top:2368px;width:293px;height:162px;background:#fff;box-shadow:0 2px 10px rgba(0,0,0,.14);text-align:center;padding:14px 10px}
.tcard::after{content:"";position:absolute;left:140px;bottom:-8px;width:14px;height:14px;background:#fff;transform:rotate(45deg);box-shadow:3px 3px 4px rgba(0,0,0,.06)}
.quote{font-family:'Exo 2',sans-serif;font-size:56px;font-weight:700;line-height:30px;height:26px;color:var(--teal)}
.tcard p{margin-top:12px;font-size:15px;line-height:24px;color:#333;white-space:nowrap}
.client{top:2548px;display:flex;align-items:center;gap:8px}
.avatar{width:50px;height:50px;border-radius:50%;background:linear-gradient(135deg,#8a8a8a,#3d3d3d)}
.client b{display:block;font-family:'Exo 2',sans-serif;font-size:15.5px;font-weight:600;color:#111}
.client small{font-size:11.5px;color:#333}

.cta-bg{top:2685px;left:0;width:1200px;height:440px;background:var(--pale)}

/* footer */
.footer{top:3110px;left:0;width:1200px;height:389px;background:var(--black);color:#fff}
.fcol{position:absolute;top:38px}
.fcol h4{font-size:21px;font-weight:600;margin-bottom:16px}
.fcol ul{list-style:none;font-size:15px;line-height:30px;padding-left:6px}
.fcol p{font-size:15px;line-height:30px;white-space:nowrap}
.fbrand{display:flex;align-items:center;gap:16px;margin-top:22px;font-family:'Exo 2',sans-serif;font-size:22px;font-weight:500}
.field{margin-top:2px;width:258px;height:36px;border:1px solid #666;border-radius:4px;display:flex;align-items:center;justify-content:space-between;padding:0 10px;font-size:14.5px;color:#888}
.fsocial{display:flex;gap:12px;margin:40px 0 0 42px}
.fsocial i{width:11px;height:11px;border-radius:50%;background:#fff;display:block}
.rule{position:absolute;left:111px;top:301px;width:980px;height:1px;background:#333}
.copy{position:absolute;top:342px;left:0;width:1200px;text-align:center;font-size:15px}
</style>
</head>
<body>
<div class="page">

  <header class="abs header">
    <div class="brand"><span class="brand-mark"></span>Ledgerwise Forge</div>
    <div class="contact">
      <span class="ico"><svg width="14" height="14" viewBox="0 0 24 24"><path fill="#14988a" d="M6.6 10.8a15 15 0 0 0 6.6 6.6l2.2-2.2a1 1 0 0 1 1-.25 11.4 11.4 0 0 0 3.6.57 1 1 0 0 1 1 1V20a1 1 0 0 1-1 1A17 17 0 0 1 3 4a1 1 0 0 1 1-1h3.5a1 1 0 0 1 1 1c0 1.25.2 2.45.57 3.6a1 1 0 0 1-.25 1z"/></svg></span>
      <span>188-555-0142</span>
      <span class="ico"><svg width="14" height="12" viewBox="0 0 24 20"><path fill="#14988a" d="M2 0h20a2 2 0 0 1 2 2v1L12 10 0 3V2a2 2 0 0 1 2-2zm-2 6 12 7 12-7v12a2 2 0 0 1-2 2H2a2 2 0 0 1-2-2z"/></svg></span>
      <span>hello@ledgerwiseforge.com</span>
      <div class="social"><i></i><i></i><i></i><i></i></div>
    </div>
    <nav class="nav">
      <a class="active" href="#">Home</a><a href="#">Services</a><a href="#">Ledgerwise Forge Method</a><a href="#">Testimonials</a><a href="#">Blog</a><a href="#">About Us</a><a href="#">Schedule Free Consultation</a>
    </nav>
  </header>

  <div class="abs hero-bg" role="img" aria-label="Dark teal background with trading candlestick chart"></div>
  <div class="abs hero-globe" role="img" aria-label="Digital globe surrounded by cryptocurrency coin symbols"></div>
  <div class="abs hero-text">
    <h1>Your own cryptocurrency Secure, easy to use, and built by an expert team</h1>
    <p>Ledgerwise Forge adds professionalism to cryptocurrency</p>
    <a class="btn" href="#"><span class="dot"><svg width="13" height="13" viewBox="0 0 16 16"><circle cx="8" cy="8" r="7.5" fill="var(--teal)"/><path d="M9 4 5 8l4 4" stroke="#fff" stroke-width="2" fill="none"/></svg></span>Learn More</a>
  </div>
  <svg class="abs" style="top:560px;left:0" width="1200" height="220" viewBox="0 0 1200 220">
    <path d="M0 170 C150 110 260 70 370 60 C200 90 90 140 0 200Z" fill="#14988a"/>
    <path d="M0 200 C120 140 260 90 420 80 C560 72 640 110 720 120 C880 140 1040 110 1200 20 L1200 60 C1050 140 900 170 720 150 C620 140 520 100 420 100 C260 100 120 160 0 230Z" fill="#14988a"/>
    <path d="M0 230 C120 165 260 108 420 106 C540 104 620 150 740 160 C900 172 1060 130 1200 50 L1200 220 L0 220Z" fill="#fff"/>
  </svg>

  <h2 class="abs title" style="top:762px">About us</h2>
  <p class="abs lead" style="top:832px;left:200px;width:800px">Ledgerwise Forge provides a complete service that handles the development, IT operations and support<br>for your cryptocurrency. Cryptocurrency development can be difficult and complex, and a quality<br>development team is hard to find and expensive.</p>
  <a class="abs btn outline" style="top:953px;left:518px" href="#"><span class="dot"><svg width="13" height="13" viewBox="0 0 16 16"><circle cx="8" cy="8" r="7.5" fill="var(--teal)"/><path d="M9 4 5 8l4 4" stroke="#fff" stroke-width="2" fill="none"/></svg></span>Learn More</a>

  <h2 class="abs title" style="top:1067px">Why choose Ledgerwise Forge</h2>
  <div class="abs feature" style="top:1172px;left:158px">
    <div class="ring"><div class="icon" role="img" aria-label="Growth chart held in hands icon"></div></div>
    <h3>Value</h3><p>A team of experts, regular updates,<br>and fixed costs</p>
  </div>
  <div class="abs feature" style="top:1172px;left:460px">
    <div class="ring green"><div class="icon" role="img" aria-label="Handshake icon"></div></div>
    <h3>Support</h3><p>Receive advice and other services,<br>beyond development.</p>
  </div>
  <div class="abs feature" style="top:1172px;left:761px">
    <div class="ring"><div class="icon" role="img" aria-label="Document with approval badge icon"></div></div>
    <h3>Commitment</h3><p>Enjoy regular updates and new<br>features.</p>
  </div>

  <svg class="abs" style="top:1500px;left:0" width="1200" height="720" viewBox="0 0 1200 720">
    <defs>
      <linearGradient id="band" x1="0" x2="1" y1="0" y2="0"><stop offset="0" stop-color="#14988a"/><stop offset="1" stop-color="#178a3a"/></linearGradient>
    </defs>
    <path d="M0 4 C120 50 240 90 420 70 C650 40 800 20 1000 40 C1100 50 1160 80 1200 110 L1200 710 C1100 650 900 620 700 650 C480 690 300 720 160 700 C90 690 40 670 0 610Z" fill="url(#band)"/>
    <path d="M120 50 C260 30 380 20 520 40 C380 60 260 80 120 50Z" fill="#d9f4f4" opacity=".9"/>
    <path d="M560 660 C700 620 900 610 1080 660 C900 700 720 700 560 660Z" fill="#d9f4f4"/>
  </svg>
  <h2 class="abs svc-title">Our Services</h2>
  <div class="abs card" style="left:111px;background:linear-gradient(160deg,#0f3b8a,#061a45)" role="img" aria-label="Blue digital network with rocket">
    <h4>Blockchain Creation<br>&amp; Launch</h4>
    <span class="btn"><span class="dot"><svg width="13" height="13" viewBox="0 0 16 16"><circle cx="8" cy="8" r="7.5" fill="var(--teal)"/><path d="M9 4 5 8l4 4" stroke="#fff" stroke-width="2" fill="none"/></svg></span>Learn More</span>
  </div>
  <div class="abs card" style="left:358px;background:linear-gradient(160deg,#2b3036,#101214)" role="img" aria-label="Hand touching hexagon technology interface">
    <h4>Blockchain<br>Development</h4>
    <span class="btn"><span class="dot"><svg width="13" height="13" viewBox="0 0 16 16"><circle cx="8" cy="8" r="7.5" fill="var(--teal)"/><path d="M9 4 5 8l4 4" stroke="#fff" stroke-width="2" fill="none"/></svg></span>Learn More</span>
  </div>
  <div class="abs card" style="left:606px;background:linear-gradient(160deg,#0c2a2a,#051010)" role="img" aria-label="Glowing green network of connected nodes">
    <h4>Blockchain<br>Operations</h4>
    <span class="btn"><span class="dot"><svg width="13" height="13" viewBox="0 0 16 16"><circle cx="8" cy="8" r="7.5" fill="var(--teal)"/><path d="M9 4 5 8l4 4" stroke="#fff" stroke-width="2" fill="none"/></svg></span>Learn More</span>
  </div>
  <div class="abs card" style="left:853px;background:linear-gradient(160deg,#3a2a3a,#0a1a3a)" role="img" aria-label="Hand holding glowing blockchain hexagons">
    <h4>Blockchain Support</h4>
    <span class="btn"><span class="dot"><svg width="13" height="13" viewBox="0 0 16 16"><circle cx="8" cy="8" r="7.5" fill="var(--teal)"/><path d="M9 4 5 8l4 4" stroke="#fff" stroke-width="2" fill="none"/></svg></span>Learn More</span>
  </div>

  <h2 class="abs title" style="top:2272px">Client Testimonials</h2>
  <div class="abs tcard" style="left:121px"><div class="quote">“</div><p>Lorem ipsum dolor sit amet,<br>consectetur adipiscing elit, sed do<br>eiusmod tempor incididunt ut labore<br>et dolore magna aliqua.</p></div>
  <div class="abs tcard" style="left:453px"><div class="quote">“</div><p>Lorem ipsum dolor sit amet,<br>consectetur adipiscing elit, sed do<br>eiusmod tempor incididunt ut labore<br>et dolore magna aliqua.</p></div>
  <div class="abs tcard" style="left:784px"><div class="quote">“</div><p>Lorem ipsum dolor sit amet,<br>consectetur adipiscing elit, sed do<br>eiusmod tempor incididunt ut labore<br>et dolore magna aliqua.</p></div>
  <div class="abs client" style="left:197px"><div class="avatar" role="img" aria-label="Client portrait"></div><div><b>Client Name</b><small>City Location</small></div></div>
  <div class="abs client" style="left:528px"><div class="avatar" role="img" aria-label="Client portrait"></div><div><b>Client Name</b><small>City Location</small></div></div>
  <div class="abs client" style="left:859px"><div class="avatar" role="img" aria-label="Client portrait"></div><div><b>Client Name</b><small>City Location</small></div></div>

  <div class="abs cta-bg"></div>
  <h2 class="abs title" style="top:2738px">Lorem Ipsum</h2>
  <p class="abs lead" style="top:2796px;left:200px;width:800px">Lorem ipsum dolor sit amet, consectetur adipiscing elit, sed do eiusmod tempor incididunt ut<br>labore et dolore magna aliqua. Quis ipsum suspendisse ultrices gravida. Risus commodo viverra<br>maecenas accumsan lacus vel facilisis.</p>
  <a class="abs btn outline" style="top:2913px;left:476px;text-transform:none" href="#"><span class="dot"><svg width="13" height="13" viewBox="0 0 16 16"><circle cx="8" cy="8" r="7.5" fill="var(--teal)"/><path d="M9 4 5 8l4 4" stroke="#fff" stroke-width="2" fill="none"/></svg></span>Schedule Free Consultation</a>

  <svg class="abs" style="top:2960px;left:0" width="1200" height="160" viewBox="0 0 1200 160">
    <path d="M0 150 C200 40 420 10 600 40 C780 70 900 80 1200 10 L1200 40 C960 110 800 110 620 70 C440 30 220 60 0 160Z" fill="#14988a"/>
    <path d="M830 130 C960 100 1080 80 1200 40 L1200 60 C1080 100 960 120 830 130Z" fill="#d6f0e4"/>
    <path d="M0 160 C220 70 440 50 620 80 C800 110 960 130 1200 60 L1200 160Z" fill="#000"/>
  </svg>

  <footer class="abs footer">
    <div class="fcol" style="left:113px">
      <h4>About us</h4>
      <p>Lorem ipsum dolor sit amet,<br>consectetur adipiscing elit, sed do<br>eiusmod tempor incididunt</p>
      <div class="fbrand"><span class="brand-mark"></span>Ledgerwise Forge</div>
    </div>
    <div class="fcol" style="left:410px">
      <h4>Quick Link</h4>
      <ul><li>Home</li><li>Services</li><li>Ledgerwise Forge Method</li><li>Testimonials</li><li>Blog</li><li>About Us</li><li>Schedule Free Consultation</li></ul>
    </div>
    <div class="fcol" style="left:659px">
      <h4>Help Link</h4>
      <ul><li>Terms&amp;condtions</li><li>Privacy Policy</li><li>About Us</li><li>Support</li></ul>
    </div>
    <div class="fcol" style="left:832px">
      <h4>Get Our Newsletter</h4>
      <div class="field"><span>Enter Your Email</span><svg width="16" height="16" viewBox="0 0 24 24"><path fill="#14988a" d="M2 11 22 2l-9 20-2-8z"/></svg></div>
      <div class="fsocial"><i></i><i></i><i></i><i></i></div>
    </div>
    <div class="rule"></div>
    <div class="copy">©Copyrights 2021 Ledgerwise Forge &nbsp;|&nbsp;&nbsp; All Rights Reserved</div>
  </footer>

</div>
</body>
</html>
```